Private Investigation Business Card Design

I need a business card for a new private investigation company named Brisk Inquiries. I perform mainly surveillance jobs, vehicle repossessions, document serves etc. The final design should aim for a professional look. The logo has a magnifying glass with stick man arms and legs and is in a running action to show the "Brisk" aspect of the name. If the colour scheme could remain the same as the website www.briskinquiries-demo.com.au with silvers,blacks and a couple electric blue highlights.
Industry/Entity Type
Business
Contact Information for Business Card
Morgan Kellaway
Brisk Inquiries
0487316204
PO Box 58, Carnwell NSW 2291
info@briskinquiries-demo.com.au
www.briskinquiries-demo.com.au
Look and feel

```html
<!DOCTYPE html>
<html lang="en">
<head>
<meta charset="utf-8">
<title>Brisk Inquiries – Business Card</title>
<link href="https://fonts.googleapis.com/css2?family=Play:wght@400;700&display=swap" rel="stylesheet">
<style>
  :root {
    --backdrop: #3a3a3a;
    --card: #fbfbfb;
    --ink: #222222;
    --text-grey: #3c3c3c;
    --brand-grey: #6e6e6e;
    --electric-blue: #1e8fff;
    --figure-light: #ededed;
    --figure-dark: #c9c9c9;
  }
  * { margin: 0; padding: 0; box-sizing: border-box; }
  html, body { width: 1200px; height: 750px; overflow: hidden; }
  body {
    background: var(--backdrop);
    font-family: "Play", sans-serif;
    position: relative;
  }
  .card {
    position: absolute;
    top: 215px;
    width: 560px;
    height: 320px;
    background: var(--card);
    overflow: hidden;
  }
  .card--front { left: 25px; }
  .card--back { left: 615px; }

  .mascot-area {
    position: absolute;
    left: 0; top: 0;
    width: 280px; height: 320px;
    background: linear-gradient(135deg, var(--figure-light), var(--figure-dark));
  }

  .contact {
    position: absolute;
    right: 30px;
    top: 34px;
    text-align: right;
    color: var(--text-grey);
  }
  .contact__name {
    font-size: 20px;
    font-weight: 700;
    color: var(--ink);
    letter-spacing: 0.3px;
    margin-bottom: 14px;
  }
  .contact__address {
    font-size: 13px;
    line-height: 17px;
    margin-bottom: 10px;
  }
  .contact__line {
    display: flex;
    justify-content: flex-end;
    align-items: center;
    gap: 9px;
    font-size: 13px;
    height: 22px;
  }
  .contact__line--phone { font-size: 14px; }
  .contact__icon { width: 14px; height: 14px; fill: var(--electric-blue); flex: none; }

  .brand-name {
    font-family: "Play", sans-serif;
    font-weight: 700;
    color: var(--brand-grey);
    white-space: nowrap;
  }
  .card--front .brand-name {
    position: absolute;
    right: 30px;
    bottom: 38px;
    font-size: 28px;
  }
  .brand-rule {
    position: absolute;
    right: 30px;
    bottom: 30px;
    width: 60px;
    height: 3px;
    background: var(--electric-blue);
  }

  .back-brand {
    position: absolute;
    left: 0; right: 0;
    top: 132px;
    display: flex;
    justify-content: center;
    align-items: center;
    gap: 14px;
  }
  .back-brand .brand-name { font-size: 38px; }
  .brand-dot {
    width: 22px; height: 22px;
    border-radius: 50%;
    background: var(--electric-blue);
  }
  .back-url {
    position: absolute;
    left: 0; right: 0;
    top: 272px;
    text-align: center;
    font-size: 13px;
    letter-spacing: 2.2px;
    color: var(--text-grey);
  }
</style>
</head>
<body>
  <section class="card card--front">
    <div class="mascot-area" role="img" aria-label="Running magnifying-glass stick figure mascot"></div>

    <div class="contact">
      <p class="contact__name">Morgan Kellaway</p>
      <p class="contact__address">PO Box 58<br>Carnwell NSW 2291</p>
      <p class="contact__line contact__line--phone">0487 316 204
        <svg class="contact__icon" viewBox="0 0 24 24" aria-hidden="true"><path d="M6.6 10.8c1.4 2.8 3.8 5.1 6.6 6.6l2.2-2.2c.3-.3.7-.4 1-.2 1.1.4 2.3.6 3.6.6.6 0 1 .4 1 1V20c0 .6-.4 1-1 1C10.6 21 3 13.4 3 4c0-.6.4-1 1-1h3.5c.6 0 1 .4 1 1 0 1.3.2 2.5.6 3.6.1.3 0 .7-.2 1L6.6 10.8z"/></svg>
      </p>
      <p class="contact__line">info@briskinquiries-demo.com.au
        <svg class="contact__icon" viewBox="0 0 24 24" aria-hidden="true"><path d="M2 5h20v14H2z M4 7v.5l8 5 8-5V7l-8 5z" fill-rule="evenodd"/></svg>
      </p>
      <p class="contact__line">www.briskinquiries-demo.com.au
        <svg class="contact__icon" viewBox="0 0 24 24" aria-hidden="true"><circle cx="12" cy="12" r="10"/><path d="M7 8c2 0 3 1 3 3s-2 2-2 4M15 5c-1 2 0 3 2 3s3 2 2 4-2 1-3 3" stroke="#fbfbfb" stroke-width="1.6" fill="none"/></svg>
      </p>
    </div>

    <p class="brand-name">Brisk Inquiries</p>
    <span class="brand-rule" aria-hidden="true"></span>
  </section>

  <section class="card card--back">
    <div class="back-brand">
      <p class="brand-name">Brisk Inquiries</p>
      <span class="brand-dot" aria-hidden="true"></span>
    </div>
    <p class="back-url">www.briskinquiries-demo.com.au</p>
  </section>
</body>
</html>
```